Veltrane Group Business Card Design

The CEO is looking for a new trendy look for his business card.
You can stay with current branding or come up with something new/creative. It can be 3D, including Medical Office buildings. You can use our logo in a variety of colors. Please include name, title, company name, company website, email address, cell number

Target Market(s)

Real Estate Development and Construction

Industry/Entity Type

Health care real estate

Contact Information for Business Card

Rohesh Kamdar, CEO M-604.781.2249 E-roheshkamdar@veltrane.com Address:4180 Lindqvist Ave, Tampa, FL 33482 www.veltrane.com

Font styles to use
Other font styles liked:
• Be creative

Requirements
Must have
• Creative, trendy look
Nice to have
• Please go to our website to get a feel- www. veltrane.com
Should not have
• small fonts

```html
<!DOCTYPE html>
<html lang="en">
<head>
<meta charset="utf-8">
<title>Veltrane Group Business Card</title>
<link rel="stylesheet" href="https://fonts.googleapis.com/css2?family=Arimo:wght@400;700&family=Jost:wght@400;500&display=swap">
<style>
  :root {
    --brand-red: #b1202a;
    --slate: #505054;
    --ink-dark: #3a3a3c;
    --paper: #ffffff;
    --backdrop-center: #3a3a3c;
    --backdrop-edge: #161616;
  }
  * { margin: 0; padding: 0; box-sizing: border-box; }
  html, body { width: 1200px; height: 1000px; overflow: hidden; }
  body {
    position: relative;
    background: radial-gradient(ellipse at center, var(--backdrop-center) 0%, var(--backdrop-edge) 100%);
    font-family: "Arimo", Arial, sans-serif;
  }
  .card {
    position: absolute;
    left: 236px;
    width: 727px;
    height: 415px;
  }
  .card-front { top: 71px; background: var(--brand-red); }
  .card-back { top: 513px; background: var(--paper); }

  .front-brand {
    position: absolute;
    top: 190px; left: 0; right: 0;
    text-align: center;
    color: var(--paper);
    font-weight: 700;
    font-size: 46px;
    letter-spacing: 1px;
  }
  .front-address {
    position: absolute;
    top: 364px; left: 0; right: 0;
    text-align: center;
    color: var(--paper);
    font-family: "Jost", Arial, sans-serif;
    font-size: 19px;
  }

  .back-brand {
    position: absolute;
    top: 90px; left: 0; right: 0;
    text-align: center;
    color: var(--brand-red);
    font-weight: 700;
    font-size: 44px;
    letter-spacing: -1px;
  }
  .holder-name {
    position: absolute;
    top: 186px; left: 0; right: 0;
    text-align: center;
    color: var(--brand-red);
    font-weight: 700;
    font-size: 31px;
  }
  .holder-title {
    position: absolute;
    top: 224px; left: 0; right: 0;
    text-align: center;
    color: var(--ink-dark);
    font-family: "Jost", Arial, sans-serif;
    font-size: 21px;
    letter-spacing: 3px;
  }
  .contact-strip {
    position: absolute;
    left: 0; right: 0; bottom: 0;
    height: 65px;
  }
  .contact-cell {
    position: absolute;
    top: 0;
    height: 65px;
    color: var(--paper);
    display: flex;
    align-items: center;
    justify-content: center;
    padding-top: 8px;
    font-size: 19px;
  }
  .contact-cell.phone { left: 0; width: 238px; background: var(--slate); }
  .contact-cell.email { left: 245px; width: 238px; background: var(--brand-red); font-size: 17px; }
  .contact-cell.web { left: 490px; width: 237px; background: var(--slate); }
  .contact-icon {
    position: absolute;
    top: -22px;
    left: 50%;
    margin-left: -19px;
    width: 38px; height: 38px;
    border-radius: 4px;
    display: flex;
    align-items: center;
    justify-content: center;
  }
  .contact-icon.red { background: var(--brand-red); }
  .contact-icon.grey { background: var(--slate); }
  .contact-icon svg { width: 20px; height: 20px; }
</style>
</head>
<body>
  <section class="card card-front">
    <div class="front-brand">Veltrane Group</div>
    <div class="front-address">4180 Lindqvist Ave, Tampa, FL 33482</div>
  </section>

  <section class="card card-back">
    <div class="back-brand">Veltrane</div>
    <div class="holder-name">ROHESH KAMDAR</div>
    <div class="holder-title">CEO</div>

    <div class="contact-strip">
      <div class="contact-cell phone">
        <span class="contact-icon red">
          <svg viewBox="0 0 20 20" fill="none" stroke="#fff" stroke-width="1.6">
            <rect x="5.5" y="2" width="9" height="16" rx="1.5"/>
            <line x1="8.5" y1="15" x2="11.5" y2="15"/>
          </svg>
        </span>
        604.781.2249
      </div>
      <div class="contact-cell email">
        <span class="contact-icon grey">
          <svg viewBox="0 0 20 20" fill="#fff">
            <path d="M2 9 L18 2 L14 18 L9.5 12.5 Z"/>
            <path d="M9.5 12.5 L18 2" stroke="#505054" stroke-width="1"/>
          </svg>
        </span>
        roheshkamdar@veltrane.com
      </div>
      <div class="contact-cell web">
        <span class="contact-icon red">
          <svg viewBox="0 0 20 20" fill="none" stroke="#fff" stroke-width="1.4">
            <circle cx="10" cy="10" r="7.5"/>
            <ellipse cx="10" cy="10" rx="3.2" ry="7.5"/>
            <line x1="2.5" y1="10" x2="17.5" y2="10"/>
          </svg>
        </span>
        www.veltrane.com
      </div>
    </div>
  </section>
</body>
</html>
```